business card design for a plumbing contractor

i need a double business card for a plumbing business, our initial service is residential Sewer Drain Cleaning.

Target Market(s)

other plumbing Business

Industry/Entity Type

Plumbing

Contact Information for Business Card

www.PipeworksTopMark.example- 5307218394-

Font styles to use
Serif

Colors
ec1f27
0455a3

```html
<!DOCTYPE html>
<html lang="en">
<head>
<meta charset="utf-8">
<title>Pipeworks Top Mark – Business Card</title>
<link rel="stylesheet" href="https://fonts.googleapis.com/css2?family=Oswald:wght@500&family=Roboto:wght@300;400;700&display=swap">
<style>
  :root {
    --backdrop: #3b3631;
    --card-back: #7b7567;
    --card-front: #ffffff;
    --brand-red: #e0262c;
    --brand-grey: #77706a;
    --text-grey: #6f6a64;
  }
  * { box-sizing: border-box; margin: 0; padding: 0; }
  html, body {
    width: 1200px; height: 930px; overflow: hidden;
    background: var(--backdrop);
    font-family: "Roboto", Arial, sans-serif;
  }
  .card {
    position: absolute;
    width: 620px; height: 354px;
    border-radius: 18px;
    box-shadow: 0 10px 28px rgba(0,0,0,.35);
  }
  .card-back {
    left: 80px; top: 80px;
    background: var(--card-back);
    display: flex; align-items: center; justify-content: center;
  }
  .card-front {
    left: 500px; top: 496px;
    background: var(--card-front);
  }
  .wordmark {
    font-family: "Roboto", Arial, sans-serif;
    font-weight: 700;
    font-size: 40px;
    line-height: 1;
    letter-spacing: .5px;
    display: flex; align-items: center; gap: 12px;
  }
  .wordmark .mark-dot {
    width: 14px; height: 14px; border-radius: 50%;
  }
  .card-back .wordmark { color: #ffffff; }
  .card-back .mark-dot { background: #ffffff; }
  .card-front .wordmark {
    position: absolute; left: 46px; top: 120px;
    font-size: 32px; color: var(--brand-grey);
  }
  .card-front .mark-dot { background: var(--brand-red); }
  .person {
    position: absolute; right: 40px; top: 40px; text-align: right;
  }
  .person-name {
    font-family: "Oswald", "Arial Narrow", sans-serif;
    font-weight: 500; font-size: 34px; color: var(--brand-red);
    text-transform: uppercase; letter-spacing: -.5px; line-height: 1;
  }
  .person-title {
    font-weight: 300; font-size: 15px; color: var(--text-grey); margin-top: 2px;
  }
  .services {
    position: absolute; right: 40px; top: 178px;
    list-style: none; text-align: right;
    font-weight: 300; font-size: 16px; color: var(--text-grey); line-height: 22px;
  }
  .services li::after {
    content: ""; display: inline-block; width: 7px; height: 7px;
    border-radius: 50%; background: var(--brand-red);
    margin-left: 10px; vertical-align: middle;
  }
  .contact {
    position: absolute; left: 46px; bottom: 32px;
    list-style: none; font-weight: 300; font-size: 15px; color: var(--text-grey);
    line-height: 21px;
  }
  .contact li { display: flex; align-items: center; gap: 8px; }
  .contact svg { width: 11px; height: 11px; flex: none; }
</style>
</head>
<body>
  <section class="card card-back">
    <div class="wordmark"><span>Pipeworks Top Mark</span><span class="mark-dot"></span></div>
  </section>

  <section class="card card-front">
    <div class="person">
      <div class="person-name">Daniel Reyes</div>
      <div class="person-title">Director</div>
    </div>

    <div class="wordmark"><span>Pipeworks Top Mark</span><span class="mark-dot"></span></div>

    <ul class="services">
      <li>Sewer Drain Cleaning</li>
      <li>Maintenance</li>
      <li>Trenchless Pipe Installs</li>
    </ul>

    <ul class="contact">
      <li>
        <svg viewBox="0 0 12 12" aria-hidden="true"><path d="M2.5 1 4.5 1 5.3 3.6 4 4.6C4.7 6 6 7.3 7.4 8L8.4 6.7 11 7.5 11 9.5C11 10.3 10.3 11 9.5 11 5 11 1 7 1 2.5 1 1.7 1.7 1 2.5 1Z" fill="#e0262c"/></svg>
        <span>5307218394</span>
      </li>
      <li>
        <svg viewBox="0 0 12 12" aria-hidden="true"><rect x="1" y="2.5" width="10" height="7" rx="1" fill="none" stroke="#e0262c" stroke-width="1.3"/><path d="M1.5 3 6 6.5 10.5 3" fill="none" stroke="#e0262c" stroke-width="1.3"/></svg>
        <span>Dispatcher@PipeworksTopMark.example</span>
      </li>
      <li>
        <svg viewBox="0 0 12 12" aria-hidden="true"><circle cx="6" cy="6" r="5" fill="none" stroke="#e0262c" stroke-width="1.2"/><path d="M1 6H11M6 1C3.5 4 3.5 8 6 11M6 1C8.5 4 8.5 8 6 11" fill="none" stroke="#e0262c" stroke-width="1"/></svg>
        <span>www.PipeworksTopMark.example</span>
      </li>
    </ul>
  </section>
</body>
</html>
```